Meal Plan Website Needs New Pages Designed

Brightwick Supper Kits is an online, membership based program that delivers weekly meal programs (7 days worth of recipes plus shopping lists) carefully crafted by an expert team of meal planners. All recipes are created to comply with the following macronutrient ratio: 65% healthy fats, 25% lean protein, 10% good carbs.
All recipes are Paleo friendly and a great resource for those individuals who want to correctly implement this type of diet.

We are re-designing our website and need the following pages designed:

· Home page w/ logo
· How it works page
· Get Started! page
· Recipes Page template (these will be the pages on our site that will have recipes)
· Kitchen Essentials Training page (this will be a page with videos and tips + tricks, PDFs, etc)

So 5 total PSDs, 1 for each page.

Target audience: Men and women between the ages of 30 and 60 who want to:
· Eat healthy
· Lose weight
· Follow/Implement the Paleo diet
· Take the guesswork out of preparing delicious AND healthy meals for them and their families
· Know exactly what to eat, what to buy, how to make it

Feelings/Messages we want to communicate through the design:
· “Organic” but elegant look
· Fresh/light/Airy
· Simple but NOT GENERIC
· “I want to get cooking” feeling

Our Stylistic preferences:
· Minimalist with a few bold elements (something in between)
· Easy to visually navigate (enough white space, but not too much)
· There is more to “see” than to “read”

Our Color Preferences:
· Lighter pallet
· Colors that evoke natural woods, granite countertops…
· Stay away from using all dark colors

Our Font Type Preferences:
· Easy to read
· Not more than 3 font types
· Not too rigid
· Not too sophisticated
· Simple with a touch

Examples of Website Designs that we like:
· http://www.dorvanta.com/meal-plans/
· http://grulvix.com/
· https://www.mistobarn.com/

```html
<!DOCTYPE html>
<html lang="en">
<head>
<meta charset="utf-8">
<title>Brightwick Supper Kits – Paleo Meal Plans</title>
<link href="https://fonts.googleapis.com/css2?family=Open+Sans:wght@400;600;700&family=Lobster&display=swap" rel="stylesheet">
<style>
:root{
  --red:#e2452e;
  --salmon:#f2866d;
  --salmon-light:#f7b3a2;
  --ink:#333333;
  --muted:#777777;
  --line:#dddddd;
  --paper:#ffffff;
  --mist:#efefef;
  --spot:#e4e4e4;
}
*{box-sizing:border-box;margin:0;padding:0}
html,body{width:1200px;height:2192px;overflow:hidden}
body{font-family:"Open Sans",Arial,sans-serif;color:var(--ink);background:var(--mist);font-size:13px;position:relative}
.block{position:absolute;left:0;width:1200px}
.inner{position:absolute;left:100px;width:1000px}

/* header */
.site-header{top:0;height:112px;background:var(--paper)}
.brand{position:absolute;left:100px;top:24px;font-family:"Lobster",cursive;font-size:30px;color:var(--red);display:flex;align-items:center;gap:10px}
.brand-dot{width:14px;height:14px;border-radius:50%;background:var(--salmon)}
.top-tools{position:absolute;right:100px;top:12px;display:flex;gap:6px}
.tool{background:var(--red);color:#fff;font-size:11px;font-weight:600;padding:6px 12px;border-radius:3px}
.main-nav{position:absolute;right:100px;top:66px;display:flex;gap:24px;font-size:11px;font-weight:700;color:var(--red);letter-spacing:.3px}

/* hero */
.hero{top:112px;height:428px;background:
  radial-gradient(ellipse 260px 150px at 880px 250px,#e8b26a 0%,#d98a45 60%,transparent 100%),
  radial-gradient(ellipse 200px 160px at 140px 330px,#7fa53a 0%,transparent 100%),
  linear-gradient(120deg,#c9d37a 0%,#f0c88e 40%,#f4d3a4 58%,#d98a55 82%,#b45f38 100%)}
.hero-copy{position:absolute;left:150px;top:40px;font-family:"Lobster",cursive;font-size:38px;line-height:46px;color:var(--red)}
.hero-copy span{display:block}
.hero-copy span:first-child{color:#fff}
.slider-dots{position:absolute;left:140px;bottom:18px;display:flex;gap:6px}
.slider-dots i{width:12px;height:12px;border-radius:50%;background:#fff;opacity:.7}
.slider-dots i:first-child{opacity:1}

/* steps */
.steps{top:540px;height:220px}
.steps .wave{position:absolute;left:0;top:0}
.step{position:absolute;top:28px;width:200px;margin-left:-100px;text-align:center}
.step-circle{width:88px;height:88px;margin:0 auto;border-radius:50%;background:var(--paper);border:3px solid var(--salmon-light);display:flex;align-items:center;justify-content:center}
.step-num{display:inline-block;margin-top:8px;width:20px;height:20px;border-radius:50%;background:var(--red);color:#fff;font-size:10px;font-weight:700;line-height:20px}
.step-label{font-family:"Lobster",cursive;color:var(--red);font-size:17px;margin-top:2px}

/* recipe finder */
.finder{top:784px;height:192px;background:var(--paper);box-shadow:0 1px 3px rgba(0,0,0,.15)}
.tabs{display:flex;height:40px}
.tab{flex:1;display:flex;align-items:center;justify-content:center;gap:8px;font-size:12px;font-weight:700;color:#fff;background:var(--red)}
.tab.active{background:var(--paper);color:var(--ink);border-bottom:1px solid var(--line)}
.finder-body{padding:24px 30px}
.finder-body h2{font-size:20px;font-weight:600;margin-bottom:20px}
.finder-row{display:flex;gap:14px;align-items:center}
.field{height:40px;border:1px solid var(--line);background:#fafafa;color:#aaa;padding:0 12px;display:flex;align-items:center;font-size:12px}
.field.ingredient{width:420px}
.field.meal{width:300px}
.btn-find{background:var(--red);color:#fff;font-weight:700;font-size:14px;height:40px;padding:0 22px;display:flex;align-items:center;gap:8px;border-radius:3px}

/* recipes strip */
.recipes{top:1010px;height:200px}
.bar{display:flex;justify-content:space-between;align-items:center;height:34px;border-bottom:2px solid var(--line);margin-bottom:16px}
.bar h3{font-size:13px;font-weight:700;color:var(--red);letter-spacing:.4px}
.arrows{display:flex;gap:3px}
.arrows i{width:18px;height:18px;background:var(--red);border-radius:3px;display:block}
.dishes{display:flex;justify-content:space-between;padding:0 20px}
.dish{width:150px;text-align:center}
.dish-photo{height:96px;border-radius:50%;position:relative;background:#fff;box-shadow:0 2px 4px rgba(0,0,0,.12)}
.dish-photo::after{content:"";position:absolute;inset:12px 22px;border-radius:50%;background:var(--food)}
.dish-tag{display:inline-block;margin-top:10px;background:var(--red);color:#fff;font-size:11px;font-weight:700;padding:5px 14px;border-radius:3px}

/* three panels */
.columns{top:1264px;height:240px;display:flex;gap:20px}
.panel{flex:1;background:var(--paper);box-shadow:0 1px 3px rgba(0,0,0,.12);padding:14px 18px;position:relative;overflow:hidden}
.panel h4{font-family:"Lobster",cursive;font-size:22px;color:var(--red);font-weight:400;margin-bottom:10px}
.chef{position:absolute;left:18px;top:52px;width:112px;height:172px;background:linear-gradient(180deg,#fafafa,#d9d9d9);border-radius:4px}
.welcome-text{margin-left:122px;font-size:11px;line-height:16px;color:var(--muted)}
.news-item{display:flex;gap:10px;margin-bottom:9px}
.thumb{width:38px;height:38px;flex:none;background:linear-gradient(135deg,#8fb04a,#d89a5a)}
.news-item p{font-size:10px;line-height:13px;color:var(--muted)}
.news-item b{display:block;color:var(--ink)}
.news-item time{color:var(--red)}
.tweet{display:flex;gap:10px;margin-bottom:12px;font-size:10px;line-height:14px;color:var(--muted)}
.tweet-icon{width:22px;height:22px;flex:none;border-radius:50%;background:var(--salmon)}
.tweet b{color:var(--red)}

/* partners */
.spots{top:1520px;height:140px}
.spots .bar h3{font-family:"Lobster",cursive;font-size:22px;font-weight:400;letter-spacing:0}
.spot-row{display:flex;justify-content:space-between;padding:10px 30px}
.spot{width:80px;height:46px;border-radius:6px;background:var(--spot)}

/* icon bar */
.iconbar{top:1820px;height:112px;background:var(--paper);border-top:1px solid var(--line);border-bottom:1px solid var(--line)}
.iconbar .inner{display:flex;height:100%}
.ib{flex:1;display:flex;flex-direction:column;align-items:center;justify-content:center;gap:12px;border-right:1px solid var(--line);font-size:11px;font-weight:700}
.ib:first-child{border-left:1px solid var(--line)}

/* footer */
.footer-band{top:1958px;height:30px;background:var(--salmon)}
.footer-main{top:1988px;height:172px}
.footer-main .inner{display:flex;gap:30px;padding-top:16px}
.fcol{width:150px}
.fcol h5{font-size:11px;font-weight:700;margin-bottom:6px}
.fcol li{list-style:none;font-size:10px;line-height:16px;color:var(--muted)}
.social{margin-left:auto;width:220px;display:flex;flex-direction:column;gap:6px}
.soc{display:flex;align-items:center;gap:8px;height:24px;background:var(--paper);border:1px solid var(--line);padding:0 8px;font-size:10px;color:var(--muted)}
.soc i{width:14px;height:14px;border-radius:2px;background:var(--salmon);display:block}
.copyright{top:2160px;height:32px;background:var(--salmon);color:#fff;text-align:center;font-size:10px;line-height:32px}
</style>
</head>
<body>

<header class="block site-header">
  <div class="brand"><span class="brand-dot"></span>Brightwick Supper Kits</div>
  <div class="top-tools">
    <span class="tool">GET STARTED NOW</span>
    <span class="tool">ENGLISH</span>
    <span class="tool">LOGIN</span>
  </div>
  <nav class="main-nav">
    <span>HOW IT WORKS</span><span>RECIPES</span><span>MEAL PLANS</span><span>KITCHEN ESSENTIALS</span><span>FAQ</span><span>MEMBERS</span><span>CONTACT</span>
  </nav>
</header>

<section class="block hero" role="img" aria-label="Photo of a plated Paleo dish with fresh salad and vegetables">
  <div class="hero-copy">
    <span>Seven days of Paleo suppers</span>
    <span>planned, portioned and listed</span>
    <span>65% fats, 25% protein, 10% carbs</span>
    <span>so all you do is get cooking</span>
  </div>
  <div class="slider-dots"><i></i><i></i><i></i><i></i></div>
</section>

<section class="block steps">
  <svg class="wave" width="1200" height="140" viewBox="0 0 1200 140"><path d="M268 72 C360 20 430 124 520 72 S650 20 740 72 S860 124 948 72" fill="none" stroke="#e2452e" stroke-width="3"/></svg>
  <div class="step" style="left:268px">
    <div class="step-circle"><svg width="36" height="36" viewBox="0 0 40 40"><rect x="8" y="5" width="24" height="30" rx="2" fill="none" stroke="#e2452e" stroke-width="3"/><path d="M13 14h14M13 20h14M13 26h9" stroke="#e2452e" stroke-width="2.5"/></svg></div>
    <span class="step-num">1</span><div class="step-label">Choose your Plan</div>
  </div>
  <div class="step" style="left:520px">
    <div class="step-circle"><svg width="36" height="36" viewBox="0 0 40 40"><path d="M13 4v32M9 4v9q4 5 8 0V4M27 4q-5 6 0 14v18" fill="none" stroke="#e2452e" stroke-width="3"/></svg></div>
    <span class="step-num">2</span><div class="step-label">Get the Recipes</div>
  </div>
  <div class="step" style="left:740px">
    <div class="step-circle"><svg width="36" height="36" viewBox="0 0 40 40"><path d="M4 8h6l4 18h18l3-12H12" fill="none" stroke="#e2452e" stroke-width="3"/><circle cx="16" cy="32" r="2.5" fill="#e2452e"/><circle cx="29" cy="32" r="2.5" fill="#e2452e"/></svg></div>
    <span class="step-num">3</span><div class="step-label">Shop the List</div>
  </div>
  <div class="step" style="left:948px">
    <div class="step-circle"><svg width="36" height="36" viewBox="0 0 40 40"><path d="M8 21l8 8 16-18" fill="none" stroke="#e2452e" stroke-width="4"/></svg></div>
    <span class="step-num">4</span><div class="step-label">Enjoy</div>
  </div>
</section>

<section class="inner finder" style="position:absolute">
  <div class="tabs">
    <div class="tab active"><svg width="12" height="16" viewBox="0 0 12 16"><path d="M6 0a6 6 0 0 1 6 6c0 4-6 10-6 10S0 10 0 6a6 6 0 0 1 6-6z" fill="#e2452e"/><circle cx="6" cy="6" r="2" fill="#fff"/></svg>SEARCH BY INGREDIENT</div>
    <div class="tab">RECIPES BY MEAL</div>
    <div class="tab">RECIPES BY GOAL</div>
  </div>
  <div class="finder-body">
    <h2>Find a Paleo recipe for this week’s meal plan!</h2>
    <div class="finder-row">
      <div class="field ingredient">Ingredient</div>
      <div class="field meal">Meal type</div>
      <div class="btn-find"><svg width="14" height="14" viewBox="0 0 14 14"><circle cx="6" cy="6" r="4.5" fill="none" stroke="#fff" stroke-width="2"/><path d="M9.5 9.5L13 13" stroke="#fff" stroke-width="2"/></svg>FIND RECIPES!</div>
    </div>
  </div>
</section>

<section class="inner recipes" style="position:absolute">
  <div class="bar"><h3>THIS WEEK’S PALEO RECIPES</h3><div class="arrows"><i></i><i></i></div></div>
  <div class="dishes">
    <div class="dish"><div class="dish-photo" style="--food:radial-gradient(circle,#f08a5d,#d8623a)" role="img" aria-label="Salmon bowl on a plate"></div><span class="dish-tag">SALMON BOWL</span></div>
    <div class="dish"><div class="dish-photo" style="--food:radial-gradient(circle,#b7743f,#7d4a26)" role="img" aria-label="Grass-fed burger on a plate"></div><span class="dish-tag">GRASS-FED BURGER</span></div>
    <div class="dish"><div class="dish-photo" style="--food:radial-gradient(circle,#a9c766,#6f9a33)" role="img" aria-label="Zucchini noodles on a plate"></div><span class="dish-tag">ZUCCHINI NOODLES</span></div>
    <div class="dish"><div class="dish-photo" style="--food:radial-gradient(circle,#e6c58a,#8fb04a)" role="img" aria-label="Chicken salad on a plate"></div><span class="dish-tag">CHICKEN SALAD</span></div>
    <div class="dish"><div class="dish-photo" style="--food:radial-gradient(circle,#a8553a,#6b2f1f)" role="img" aria-label="Grilled steak on a plate"></div><span class="dish-tag">GRILLED STEAK</span></div>
  </div>
</section>

<section class="inner columns" style="position:absolute">
  <article class="panel">
    <h4>Welcome!</h4>
    <div class="chef" role="img" aria-label="Photo of a chef in white uniform holding a plated dish"></div>
    <p class="welcome-text">Brightwick Supper Kits is a membership of weekly Paleo meal plans: seven days of recipes plus a shopping list, crafted by our expert planners so you know exactly what to buy, what to make and how to make it.</p>
  </article>
  <article class="panel">
    <h4>Hot News!</h4>
    <div class="news-item"><div class="thumb" role="img" aria-label="Food photo"></div><p><b>New week of spring recipes</b>Seven fresh suppers with seasonal greens. <time>Feb 07, 2014</time></p></div>
    <div class="news-item"><div class="thumb" role="img" aria-label="Food photo"></div><p><b>Kitchen essentials videos</b>Knife skills and batch cooking tips added. <time>Feb 05, 2014</time></p></div>
    <div class="news-item"><div class="thumb" role="img" aria-label="Food photo"></div><p><b>Printable shopping lists</b>Download every list as a tidy PDF. <time>Feb 03, 2014</time></p></div>
    <div class="news-item"><div class="thumb" role="img" aria-label="Food photo"></div><p><b>Family size portions</b>Scale any plan to feed four or six. <time>Feb 01, 2014</time></p></div>
  </article>
  <article class="panel">
    <h4>Hot Tweets!</h4>
    <div class="tweet"><span class="tweet-icon"></span><p><b>@BrightwickKits</b> This week’s plan is live: seven Paleo suppers and one list. <b>2 hours ago</b></p></div>
    <div class="tweet"><span class="tweet-icon"></span><p><b>@BrightwickKits</b> Tip: roast a tray of vegetables on Sunday for quick lunches. <b>5 hours ago</b></p></div>
    <div class="tweet"><span class="tweet-icon"></span><p><b>@BrightwickKits</b> Our members lost 6 pounds on average in their first month. <b>1 day ago</b></p></div>
    <div class="tweet"><span class="tweet-icon"></span><p><b>@BrightwickKits</b> New video: how to stock a simple Paleo pantry at home. <b>2 days ago</b></p></div>
  </article>
</section>

<section class="inner spots" style="position:absolute">
  <div class="bar"><h3>Hot Spots!</h3><div class="arrows"><i></i><i></i></div></div>
  <div class="spot-row">
    <span class="spot"></span><span class="spot"></span><span class="spot"></span><span class="spot"></span><span class="spot"></span><span class="spot"></span><span class="spot"></span><span class="spot"></span>
  </div>
</section>

<nav class="block iconbar">
  <div class="inner" style="top:0">
    <div class="ib"><svg width="28" height="28" viewBox="0 0 30 30"><circle cx="15" cy="9" r="6" fill="#333"/><path d="M3 29a12 12 0 0 1 24 0z" fill="#333"/></svg>ABOUT</div>
    <div class="ib"><svg width="28" height="28" viewBox="0 0 30 30"><path d="M7 3l5 6-3 3q3 6 9 9l3-3 6 5-3 5Q14 28 2 8z" fill="#333"/></svg>CONTACT</div>
    <div class="ib"><svg width="28" height="28" viewBox="0 0 30 30"><path d="M9 3v24M5 3v8q4 5 8 0V3M22 3q-6 7 0 14v10" fill="none" stroke="#333" stroke-width="3"/></svg>RECIPES</div>
    <div class="ib"><svg width="28" height="28" viewBox="0 0 30 30"><path d="M3 12L15 4l12 8v15H3z" fill="#333"/><rect x="12" y="18" width="6" height="9" fill="#fff"/></svg>KITCHEN</div>
    <div class="ib"><svg width="28" height="28" viewBox="0 0 30 30"><path d="M2 5h5l3 14h14l3-10H9" fill="none" stroke="#333" stroke-width="3"/><circle cx="12" cy="25" r="2.5" fill="#333"/><circle cx="23" cy="25" r="2.5" fill="#333"/></svg>SHOPPING LISTS</div>
    <div class="ib"><svg width="28" height="28" viewBox="0 0 30 30"><rect x="8" y="2" width="14" height="26" rx="2" fill="#333"/><rect x="10" y="5" width="10" height="17" fill="#fff"/></svg>MOBILE APPS</div>
  </div>
</nav>

<div class="block footer-band"></div>
<footer class="block footer-main">
  <div class="inner" style="top:0">
    <div class="fcol"><h5>INFORMATION</h5><ul><li>Terms and conditions</li><li>Privacy Policy</li><li>FAQ</li><li>Customer Service</li><li>Account</li><li>Blog</li></ul></div>
    <div class="fcol"><h5>MEAL PLANS</h5><ul><li>Breakfast</li><li>Lunch</li><li>Dinner</li><li>Snacks</li><li>Desserts</li><li>All Plans</li></ul></div>
    <div class="fcol"><h5>USEFUL LINKS</h5><ul><li>How it works</li><li>Get Started</li><li>Kitchen Essentials</li><li>Shopping Lists</li><li>Members</li></ul></div>
    <div class="fcol"><h5>RECIPES</h5><ul><li>Beef</li><li>Chicken</li><li>Seafood</li><li>Vegetables</li><li>Salads</li><li>All Recipes</li></ul></div>
    <div class="social">
      <div class="soc"><i></i>Follow us on Chatterbox</div>
      <div class="soc"><i></i>Follow us on Pipwire</div>
      <div class="soc"><i></i>Follow us on Orbitly</div>
      <div class="soc"><i></i>Follow our Blog</div>
    </div>
  </div>
</footer>
<div class="block copyright">© 2014 Brightwick Supper Kits. All Rights Reserved.</div>

</body>
</html>
```